Landing Page Design for Adult Dating Age Verification (18+)

The objective of this task is to design a visually appealing pre-landing page for the adult dating site "Quillmera (site: https://quillmera.com/)" with an age verification mechanism. The pre-landing page will feature two buttons that redirect visitors to the main offer. The design should also include a footer block that includes links to the terms of use, privacy policy, and contact us pages.

Design Requirements:
Develop an age verification section prominently displayed on the pre-landing page.
Design the section to include two buttons labeled "Yes" and "No" for visitors to confirm their age.
Ensure the section is visually appealing and clearly communicates the purpose of age verification.

Visual Appeal:
Create a visually appealing design that aligns with the branding and theme of the "Quillmera" adult dating site.
Use suitable color schemes, typography, and graphics to enhance the overall visual appeal of the pre-landing page.

Layout and Navigation:
Design an engaging and intuitive layout that encourages visitors to interact with the page and proceed to the main offer.
Ensure clear and visible navigation elements that direct visitors to the main offer or provide additional information.

Responsive Design:
Develop a responsive design that provides a seamless user experience across various devices, including desktop and mobile.
Ensure the design elements and layout adapt well to different screen sizes and resolutions.

File Formats and Assets:
Deliver the final design in PSD, AI, or Sketch format, ensuring that the files are well-organized and layered.
Include any necessary images or assets used in the design, ensuring they are of high quality and optimized for web use.

```html
<!DOCTYPE html>
<html lang="en">
<head>
<meta charset="utf-8">
<title>Quillmera — Age Verification</title>
<link rel="stylesheet" href="https://fonts.googleapis.com/css2?family=Playfair+Display:wght@800&family=Nunito:wght@300;400&display=swap">
<style>
  :root {
    --board: #3d0e2d;
    --desktop-bg: #f1ebe8;
    --mobile-bg: #ffffff;
    --plum: #8e4e8f;
    --lilac: #d5b6d8;
    --ink: #1f1b1d;
    --ink-soft: #3a3436;
    --photo-dark: #3e2c2a;
    --photo-mid: #7a5a52;
    --photo-warm: #a9847a;
  }
  * { box-sizing: border-box; margin: 0; padding: 0; }
  html, body { width: 1200px; height: 593px; overflow: hidden; }
  body { background: var(--board); position: relative; font-family: "Nunito", sans-serif; }

  .desktop {
    position: absolute; left: 39px; top: 45px; width: 852px; height: 454px;
    background: var(--desktop-bg); overflow: hidden;
  }
  .desktop .hero-heart { position: absolute; left: 0; top: 0; width: 852px; height: 454px; }

  .brand { display: flex; align-items: center; gap: 6px; color: var(--ink-soft); font-family: "Nunito", sans-serif; font-weight: 400; letter-spacing: 0.5px; }
  .brand-dot { border-radius: 50%; background: var(--lilac); }

  .desktop .brand { position: absolute; left: 50px; top: 44px; font-size: 17px; }
  .desktop .brand-dot { width: 18px; height: 18px; }

  .headline { font-family: "Playfair Display", serif; font-weight: 800; color: var(--plum); }
  .desktop .headline { position: absolute; left: 46px; top: 104px; font-size: 45px; line-height: 51px; letter-spacing: -0.5px; }

  .lead { font-weight: 300; color: var(--ink); }
  .desktop .lead { position: absolute; left: 47px; top: 223px; font-size: 24px; line-height: 30px; width: 240px; }

  .actions { display: flex; }
  .btn {
    display: flex; align-items: center; justify-content: center;
    background: var(--plum); color: #fff; font-weight: 300; text-decoration: none;
  }
  .desktop .actions { position: absolute; left: 50px; top: 339px; gap: 10px; }
  .desktop .btn { width: 88px; height: 35px; border-radius: 17px; font-size: 19px; }

  .legal { color: var(--ink-soft); font-weight: 300; }
  .legal a { color: inherit; text-decoration: none; }
  .desktop .legal { position: absolute; left: 50px; top: 418px; font-size: 10.5px; white-space: nowrap; }
  .sep { margin: 0 4px; }

  .mobile {
    position: absolute; left: 918px; top: 45px; width: 235px; height: 509px;
    background: var(--mobile-bg); overflow: hidden; text-align: center;
  }
  .mobile .brand { position: absolute; left: 0; right: 0; top: 18px; justify-content: center; font-size: 13px; }
  .mobile .brand-dot { width: 14px; height: 14px; }
  .mobile .hero-heart { position: absolute; left: 0; top: 0; width: 235px; height: 290px; }
  .mobile .headline { position: absolute; left: 0; right: 0; top: 303px; font-size: 20.5px; line-height: 25px; }
  .mobile .lead { position: absolute; left: 0; right: 0; top: 363px; font-size: 11.4px; line-height: 14.5px; }
  .mobile .actions { position: absolute; left: 0; right: 0; top: 405px; justify-content: center; gap: 7px; }
  .mobile .btn { width: 47px; height: 19px; border-radius: 10px; font-size: 10.5px; }
  .mobile .legal { position: absolute; left: 0; right: 0; font-size: 8.6px; }
  .mobile .legal-links { top: 457px; }
  .mobile .legal-copy { top: 478px; }
</style>
</head>
<body>

<section class="desktop" aria-label="Desktop age verification">
  <svg class="hero-heart" viewBox="0 0 1500 800" aria-hidden="false">
    <defs>
      <linearGradient id="photoToneDesk" x1="0" y1="0" x2="1" y2="1">
        <stop offset="0" stop-color="var(--photo-dark)"/>
        <stop offset="0.55" stop-color="var(--photo-mid)"/>
        <stop offset="1" stop-color="var(--photo-warm)"/>
      </linearGradient>
    </defs>
    <path fill="var(--lilac)" d="M1047 785 L658 404 A250 250 0 1 1 1047 97 A250 250 0 1 1 1436 404 Z"/>
    <path role="img" aria-label="Photo of an embracing couple in a loft bedroom" fill="url(#photoToneDesk)"
      transform="translate(1047 695) scale(0.796) translate(-1047 -785)"
      d="M1047 785 L658 404 A250 250 0 1 1 1047 97 A250 250 0 1 1 1436 404 Z"/>
  </svg>

  <div class="brand"><span class="brand-dot"></span><span class="brand-name">Quillmera</span></div>

  <h1 class="headline">Are you over<br>the age of 18?</h1>
  <p class="lead">You must be 18 or over to view content on this page</p>

  <div class="actions">
    <a class="btn btn-yes" href="https://quillmera.com/">Yes</a>
    <a class="btn btn-no" href="#">No</a>
  </div>

  <footer class="legal">
    <a href="#">Terms of use</a><span class="sep">&nbsp;|</span>
    <a href="#">Privacy Policy</a><span class="sep">|</span>
    <a href="#">Contact us</a><span class="sep">|</span>
    <span>Copyright © 2023 All Rights Reserved</span>
  </footer>
</section>

<section class="mobile" aria-label="Mobile age verification">
  <svg class="hero-heart" viewBox="0 0 414 511">
    <defs>
      <linearGradient id="photoToneMob" x1="0" y1="0" x2="1" y2="1">
        <stop offset="0" stop-color="var(--photo-dark)"/>
        <stop offset="0.55" stop-color="var(--photo-mid)"/>
        <stop offset="1" stop-color="var(--photo-warm)"/>
      </linearGradient>
    </defs>
    <path fill="var(--lilac)" transform="translate(207 503) scale(0.491) translate(-1047 -785)"
      d="M1047 785 L658 404 A250 250 0 1 1 1047 97 A250 250 0 1 1 1436 404 Z"/>
    <path role="img" aria-label="Photo of an embracing couple in a loft bedroom" fill="url(#photoToneMob)"
      transform="translate(207 460) scale(0.397) translate(-1047 -785)"
      d="M1047 785 L658 404 A250 250 0 1 1 1047 97 A250 250 0 1 1 1436 404 Z"/>
  </svg>

  <div class="brand"><span class="brand-dot"></span><span class="brand-name">Quillmera</span></div>

  <h2 class="headline">Are you over<br>the age of 18?</h2>
  <p class="lead">You must be 18 or over to view<br>content on this page</p>

  <div class="actions">
    <a class="btn btn-yes" href="https://quillmera.com/">Yes</a>
    <a class="btn btn-no" href="#">No</a>
  </div>

  <p class="legal legal-links">
    <a href="#">Terms of use</a><span class="sep">&nbsp;|</span>
    <a href="#">Privacy Policy</a><span class="sep">|</span>
    <a href="#">Contact us</a>
  </p>
  <p class="legal legal-copy">Copyright © 2023 All Rights Reserved</p>
</section>

</body>
</html>
```